Mosquito Yard, Garden & Event Care

The uploaded logo must be integrated as the main theme of the card. I would like it to be modern and eye catching. Maybe some backround images or light silver metallic background.
Space enough at the base for contact info to be put in- phone numbers,emails,names,website.
Space on the back for short blog and lines for hand writing..calling card.
Commercial- golf courses, schools, outdoor function properties, pre event treatments.
Residential- retirement villages, townhome complexes and general houses
Management

```html
<!DOCTYPE html>
<html lang="en">
<head>
<meta charset="utf-8">
<title>Bayline Pest Co – Business Card</title>
<link rel="stylesheet" href="https://fonts.googleapis.com/css2?family=Cinzel:wght@400;500&display=swap">
<style>
  :root {
    --stage: #3b3b3c;
    --silver-light: #f7f7f7;
    --silver-mid: #d9d9d9;
    --silver-dark: #b9b9b9;
    --ink: #1f2024;
    --band: #202126;
    --mint: #4dfca5;
    --mint-soft: #8ff7c4;
    --rule: #555;
    --on-band: #f2f2f2;
  }
  * { margin: 0; padding: 0; box-sizing: border-box; }
  html, body {
    width: 1105px; height: 1200px; overflow: hidden;
    background: var(--stage);
    font-family: "Cinzel", "Times New Roman", serif;
  }
  .canvas { position: relative; width: 1105px; height: 1200px; }
  .card {
    position: absolute; left: 193px; width: 725px; height: 414px;
    overflow: hidden;
    background: radial-gradient(ellipse at 55% 45%, var(--silver-light) 0%, var(--silver-mid) 55%, var(--silver-dark) 100%);
  }
  .card--front { top: 145px; }
  .card--back { top: 601px; }

  .brand { position: absolute; color: var(--ink); }
  .brand__name {
    display: flex; align-items: center; gap: 12px;
    font-size: 36px; font-weight: 400; line-height: 1; letter-spacing: 0.5px;
    white-space: nowrap;
  }
  .brand__dot { width: 16px; height: 16px; border-radius: 50%; background: var(--mint); }
  .brand__tagline { font-size: 12.5px; letter-spacing: 0.6px; margin-top: 4px; white-space: nowrap; }
  .card--front .brand { left: 26px; top: 40px; }
  .card--back .brand { left: 0; right: 0; top: 302px; display: flex; flex-direction: column; align-items: center; }

  .person { position: absolute; left: 28px; top: 164px; }
  .person__name { color: var(--mint); font-size: 27px; letter-spacing: 1px; line-height: 1.1; }
  .person__role { color: var(--ink); font-size: 22px; margin-top: 6px; }

  .contact-band {
    position: absolute; left: 0; right: 0; bottom: 0; height: 124px;
    background: var(--band);
    border-top: 3px solid var(--mint);
  }
  .contact-list { position: absolute; left: 30px; top: 20px; list-style: none; }
  .contact-list li {
    display: flex; align-items: center; gap: 10px;
    color: var(--on-band); font-size: 18px; letter-spacing: 0.6px; height: 31px;
    white-space: nowrap;
  }
  .contact-list svg { width: 16px; height: 16px; flex: none; }
  .band-art {
    position: absolute; right: 0; bottom: 0; width: 220px; height: 124px;
    background: linear-gradient(160deg, var(--mint) 0%, var(--mint-soft) 100%);
  }

  .write-lines { position: absolute; left: 28px; right: 32px; top: 0; }
  .write-lines span {
    position: absolute; left: 0; right: 0; height: 0;
    border-top: 1.5px dotted var(--rule);
  }
</style>
</head>
<body>
<main class="canvas">
  <section class="card card--front" aria-label="Card front">
    <div class="brand">
      <div class="brand__name"><span>Bayline Pest Co</span><span class="brand__dot"></span></div>
      <div class="brand__tagline">YARD, GARDEN &amp; EVENT CARE</div>
    </div>
    <div class="person">
      <div class="person__name">LIAM CARTER</div>
      <div class="person__role">CEO/Founder</div>
    </div>
    <div class="contact-band">
      <ul class="contact-list">
        <li>
          <svg viewBox="0 0 16 16" aria-hidden="true"><path fill="#4dfca5" d="M3.6 1.5l2.2 2.7-1.3 1.6c.9 2 2.6 3.7 4.6 4.6l1.6-1.3 2.7 2.2-1.2 2.4C6.6 13.3 2.7 9.4 1.2 3.8z"/></svg>
          555 210 4786
        </li>
        <li>
          <svg viewBox="0 0 16 16" aria-hidden="true"><rect x="1" y="3" width="14" height="10" fill="#4dfca5"/><path d="M1.5 3.5L8 9l6.5-5.5" fill="none" stroke="#202126" stroke-width="1.3"/></svg>
          HELLO@BAYLINE.COM
        </li>
        <li>
          <svg viewBox="0 0 16 16" aria-hidden="true"><circle cx="8" cy="8" r="7" fill="#4dfca5"/><path d="M1 8h14M8 1c-3 3.5-3 10.5 0 14M8 1c3 3.5 3 10.5 0 14" fill="none" stroke="#202126" stroke-width="1"/></svg>
          WWW.BAYLINE.COM
        </li>
      </ul>
      <div class="band-art" role="img" aria-label="Large mint insect illustration"></div>
    </div>
  </section>

  <section class="card card--back" aria-label="Card back">
    <div class="write-lines" aria-hidden="true">
      <span style="top:55px"></span>
      <span style="top:108px"></span>
      <span style="top:157px"></span>
      <span style="top:206px"></span>
      <span style="top:264px"></span>
    </div>
    <div class="brand">
      <div class="brand__name"><span>Bayline Pest Co</span><span class="brand__dot"></span></div>
      <div class="brand__tagline">YARD, GARDEN &amp; EVENT CARE</div>
    </div>
  </section>
</main>
</body>
</html>
```